Innovative Webpage for leadership development and training company

Bright Harbor is a company supporting small organisations, in particular NGOs or projects, to increase the impact of their training and to increase the retention of talent through customized leadership development solutions. We help organisations to Guide Forward & Coach Forward
We want to have a simple but modern design webpage that stands outs from the usual consulting webpages
Here you are two possible examples of consulting firms approaching the same target audience
http://www.marlowquill.example/
http://zephvantro.example/#intro
The webpage should be designed and developed in a platform that allows full customization in the future both in terms of pages, text and images
It should allow the integration of two short videos that are currently under development
It should allow the maximum possible interoperabililty with tables and smartphones

Target Market(s)

Nonprofit, young professionals, technical assistance and capacity building projects, global SMEs, multicultural teals

Industry/Entity Type

Leadership

Number of Pages Required

5+ page

Requirements
Must have
• A dynamic/engaging/modern homepage
• A design that can be easily transferable to other pages
• A user-friendly platform that allows complete customization
• Evaluation Criteria
• 1. Overall Design/Feel of the webpage (in particular homepage). Our company looks for innovative leadership development and training. We often step out of our comfort zone in a playful positive way and that requires courage.
• 2. Flexibility to edit and/or translate homepage design to new/other pages
• 3. User-friendliness to customize, change the webpage
• 4. Completeness of coded pages (# of pages effectively developed)
Nice to have
• The maximum number of coded pages designed as per the attached file

```html
<!DOCTYPE html>
<html lang="en">
<head>
<meta charset="utf-8">
<title>Bright Harbor — Consulting · Training · Coaching</title>
<link rel="stylesheet" href="https://fonts.googleapis.com/css2?family=Raleway:wght@400;500;700&family=Open+Sans:ital,wght@0,400;0,600;1,400&display=swap">
<style>
:root{
  --orange:#ff6a00;
  --ink:#222222;
  --dark:#1b1b1b;
  --line:#e3e3e3;
  --white:#ffffff;
  --blue:#1f6fb8;
  --client-blue:#1d4f91;
  --client-grey:#5f6a75;
  --client-navy:#23406e;
  --client-ink:#2c3440;
}
*{box-sizing:border-box;margin:0;padding:0}
html,body{width:1200px;height:3186px;overflow:hidden}
body{position:relative;background:var(--white);font-family:"Open Sans",Arial,sans-serif;color:var(--ink)}
.abs{position:absolute}
.heading{font-family:"Raleway",Arial,sans-serif;font-weight:500}
.btn{position:absolute;display:flex;align-items:center;justify-content:center;font-size:11px;font-weight:600;color:var(--white);background:var(--orange)}
.btn--dark{background:#111}

/* header */
.site-header{top:0;left:0;width:1200px;height:112px;background:var(--white)}
.brand-box{top:0;left:161px;width:128px;height:127px;background:var(--white);box-shadow:0 2px 8px rgba(0,0,0,.25);z-index:5;display:flex;flex-direction:column;align-items:center;justify-content:center}
.brand-mark{width:40px;height:40px;border-radius:50%;background:var(--orange);margin-bottom:7px}
.brand-name{font-family:"Raleway",sans-serif;font-weight:700;font-size:16px;color:#111;line-height:1}
.brand-tag{font-size:7px;color:#555;margin-top:4px}
.main-nav{top:75px;left:518px;display:flex;font-size:12px;color:#777}
.main-nav .sep{margin:0 18px;color:#aaa}
.main-nav .is-active{color:var(--orange)}

/* hero */
.hero{top:112px;left:0;width:1200px;height:600px;background:radial-gradient(ellipse 520px 420px at 52% 30%,#8e9297 0%,#5d6167 45%,#2f3236 80%,#24262a 100%)}
.hero-title{top:306px;left:161px;font-family:"Raleway",sans-serif;font-weight:700;font-size:48px;line-height:1;color:var(--orange);white-space:nowrap}
.hero-title em{font-family:"Open Sans",sans-serif;font-weight:400;font-size:21px;color:var(--blue);margin-left:6px}
.hero-sub{top:368px;left:161px;font-size:13px;color:#a8a8a8}
.hero-text{top:398px;left:161px;width:405px;font-size:11.5px;line-height:1.6;color:#eeeeee}

/* about */
.about{top:712px;left:0;width:1200px;height:373px;background:var(--orange)}
.about-photo{top:771px;left:161px;width:353px;height:270px;background:radial-gradient(ellipse 260px 220px at 50% 35%,#7b8594 0%,#3d434d 50%,#14161a 100%)}
.about-title{top:776px;left:535px;font-size:30px;color:#111}
.about-lead{top:828px;left:537px;width:490px;font-size:12px;line-height:1.55;color:#111}
.about-text{top:896px;left:537px;width:490px;font-size:10.5px;line-height:1.55;color:#111}

/* services */
.section-title{left:0;width:1200px;text-align:center;font-size:30px;color:var(--orange)}
.service{top:1209px;width:300px;text-align:center}
.service-photo{width:186px;height:186px;border-radius:50%;margin:0 auto}
.service-photo--a{border:3px solid var(--orange);background:radial-gradient(circle at 55% 40%,#f6f3ef 0%,#c9c3bb 45%,#4a4e57 100%)}
.service-photo--b{background:radial-gradient(circle at 45% 35%,#fbfbfb 0%,#c4cad0 50%,#4f5863 100%)}
.service-photo--c{background:radial-gradient(circle at 50% 30%,#ffffff 0%,#d7dbe0 45%,#6b7480 100%)}
.service-name{margin-top:16px;font-family:"Open Sans",sans-serif;font-weight:400;font-size:15px;color:#222}
.service-name--accent{color:var(--orange)}
.service-text{margin:7px auto 0;width:230px;font-size:9.5px;line-height:1.5;color:#444}
.divider{top:1589px;left:0;width:1200px;height:1px;background:var(--line)}

/* videos */
.video-title strong{font-weight:700}
.video-band{top:1716px;left:0;width:1200px;height:395px;background:var(--orange)}
.video{top:1765px;height:298px;display:flex;align-items:center;justify-content:center;flex-direction:column}
.video--side{background:radial-gradient(ellipse 260px 200px at 50% 45%,#6d7177 0%,#44474c 55%,#26282b 100%)}
.video--main{background:radial-gradient(ellipse 300px 220px at 50% 40%,#ffffff 0%,#dfe3e7 45%,#8c949d 100%)}
.play-label{margin-top:10px;font-size:13px;color:var(--orange)}

/* clients */
.clients-sub{top:2214px;left:0;width:1200px;text-align:center;font-size:11px;line-height:1.6;color:#555}
.clients-arrows{top:2272px;left:1020px}
.clients-box{top:2296px;left:161px;width:878px;height:151px;border:1px solid var(--line);display:flex;align-items:center;justify-content:space-around;padding:0 10px}
.client{display:flex;align-items:center;gap:9px;font-family:"Open Sans",sans-serif;font-weight:400;font-size:18px;white-space:nowrap}
.client--a{color:var(--client-blue)}
.client--b{color:var(--client-grey)}
.client--c{color:var(--client-navy)}
.client--d{color:var(--client-ink)}
.client-dot{width:24px;height:24px;border-radius:50%;background:var(--client-blue)}
.client-square{width:22px;height:22px;background:var(--client-navy)}

/* testimonials */
.testimonials{top:2506px;left:0;width:1200px;height:463px;background:var(--dark)}
.quote-icon{top:2622px;left:577px}
.quote-text{top:2682px;left:250px;width:700px;text-align:center;font-style:italic;font-size:12px;line-height:1.75;color:#ddd}
.avatar{top:2760px;left:563px;width:74px;height:74px;border-radius:50%;border:3px solid var(--orange);background:radial-gradient(circle at 50% 40%,#f3f3f3 0%,#d8cfc7 55%,#9a8f86 100%)}
.person-name{top:2856px;left:0;width:1200px;text-align:center;font-size:12px;font-weight:600;color:var(--orange)}
.person-role{top:2882px;left:0;width:1200px;text-align:center;font-size:9.5px;color:#bbb}
.dots{top:2935px;left:570px;display:flex;gap:9px}
.dot{width:15px;height:15px;border-radius:50%;background:#ddd}
.dot--on{background:var(--orange)}

/* footer */
.footer-brand{top:3010px;left:0;width:1200px;display:flex;flex-direction:column;align-items:center}
.footer-mark{width:30px;height:30px;border-radius:50%;background:var(--orange);margin-bottom:5px}
.footer-name{font-family:"Raleway",sans-serif;font-weight:700;font-size:17px;color:#111;line-height:1}
.footer-tag{font-size:7px;color:#555;margin-top:3px}
.socials{top:3096px;left:557px;display:flex;gap:8px}
.social{width:22px;height:22px;border-radius:50%;background:#1e4f8f}
.social--muted{background:#9aa3ad}
.footer-mail{top:3126px;left:0;width:1200px;text-align:center;font-size:10px;color:#444}
.footer-line{top:3155px;left:0;width:1200px;height:1px;background:var(--line)}
.copyright{top:3164px;left:0;width:1200px;text-align:center;font-size:9px;color:#777}
</style>
</head>
<body>

<header class="abs site-header">
  <div class="abs brand-box">
    <div class="brand-mark"></div>
    <div class="brand-name">Bright Harbor</div>
    <div class="brand-tag">Consulting · Training · Coaching</div>
  </div>
  <nav class="abs main-nav">
    <span class="is-active">Home</span><span class="sep">/</span>
    <span>About Us</span><span class="sep">/</span>
    <span>Services</span><span class="sep">/</span>
    <span>Testimonials</span><span class="sep">/</span>
    <span>Blog</span><span class="sep">/</span>
    <span>Contact Us</span>
  </nav>
</header>

<section class="abs hero" role="img" aria-label="Trainer presenting at a flip chart to a seated team in a meeting room"></section>
<h1 class="abs hero-title">Bright<em>Harbor</em></h1>
<p class="abs hero-sub">Consulting - Training - Coaching</p>
<p class="abs hero-text">Bright Harbor Sprl. offers tailor made innovative solutions for organisational and individual excellence. We strive to transform the capacity and impact of non-profit organizations.</p>
<a class="btn" style="top:474px;left:161px;width:119px;height:38px">Read More</a>

<section class="abs about"></section>
<div class="abs about-photo" role="img" aria-label="Group of business professionals in suits standing together"></div>
<h2 class="abs heading about-title">Who We Are ?</h2>
<p class="abs about-lead">Bright Harbor Sprl. offers tailor made innovative solutions for organisational and individual excellence. We strive to transform the capacity and impact of non-profit organizations</p>
<p class="abs about-text">Bright Harbor Sprl. offers tailor made innovative solutions for organisational and individual excellence. We strive to transform the capacity and impact of non-profit organizations, international development and public-private projects and SMEs through customised services in leadership development, executive coaching and training.</p>
<a class="btn btn--dark" style="top:977px;left:537px;width:119px;height:36px">Read More</a>

<h2 class="abs heading section-title" style="top:1138px">Our Services</h2>
<div class="abs service" style="left:150px">
  <div class="service-photo service-photo--a" role="img" aria-label="Manager in a suit working with a colleague at a desk"></div>
  <h3 class="service-name service-name--accent">Organisational Development</h3>
  <p class="service-text">Bright Harbor's leadership and management development programs help managers develop themselves...</p>
</div>
<div class="abs service" style="left:449px">
  <div class="service-photo service-photo--b" role="img" aria-label="Coach presenting at a flip chart"></div>
  <h3 class="service-name">Executive Coaching</h3>
  <p class="service-text">Bright Harbor's coaching programs, face to face or by call, help middle managers and senior leaders...</p>
</div>
<div class="abs service" style="left:750px">
  <div class="service-photo service-photo--c" role="img" aria-label="Trainer leading a session with seated participants"></div>
  <h3 class="service-name">Training</h3>
  <p class="service-text">His experience includes coaching senior leaders working in multicultural teams in banking, insurance, trade...</p>
</div>
<a class="btn btn--dark" style="top:1489px;left:263px;width:74px;height:30px">Read More</a>
<a class="btn" style="top:1489px;left:562px;width:74px;height:30px">Read More</a>
<a class="btn" style="top:1489px;left:863px;width:74px;height:30px">Read More</a>
<div class="abs divider"></div>

<h2 class="abs heading section-title video-title" style="top:1639px">View Our <strong>Training Video</strong></h2>
<section class="abs video-band"></section>
<div class="abs video video--side" style="left:0;width:380px" role="img" aria-label="Video still of a team meeting">
  <svg width="62" height="44" viewBox="0 0 62 44"><rect width="62" height="44" rx="8" fill="#fff"/><path d="M24 12 L42 22 L24 32 Z" fill="#222"/></svg>
</div>
<div class="abs video video--main" style="left:380px;width:440px" role="img" aria-label="Video still of smiling colleagues around a meeting table">
  <svg width="62" height="44" viewBox="0 0 62 44"><rect width="62" height="44" rx="8" fill="#ff6a00"/><path d="M24 12 L42 22 L24 32 Z" fill="#fff"/></svg>
  <span class="play-label">Click here To Play</span>
</div>
<div class="abs video video--side" style="left:820px;width:380px" role="img" aria-label="Video still of a team meeting">
  <svg width="62" height="44" viewBox="0 0 62 44"><rect width="62" height="44" rx="8" fill="#fff"/><path d="M24 12 L42 22 L24 32 Z" fill="#222"/></svg>
</div>

<h2 class="abs heading section-title" style="top:2163px">Our Clients</h2>
<p class="abs clients-sub">Non-profit organizations: Many NGOs have an international or global mandate supported by a slim<br>organizational structure.</p>
<svg class="abs clients-arrows" width="18" height="14" viewBox="0 0 18 14"><path d="M7 2 L2 7 L7 12" stroke="#ff6a00" stroke-width="2" fill="none"/><path d="M11 2 L16 7 L11 12" stroke="#ff6a00" stroke-width="2" fill="none"/></svg>
<div class="abs clients-box">
  <div class="client client--a"><span class="client-dot"></span>Ridgeline Civic Alliance</div>
  <div class="client client--b">Kestrel for nonprofits</div>
  <div class="client client--c"><span class="client-square"></span>tallow peak</div>
  <div class="client client--d">Clearview Aid</div>
</div>

<section class="abs testimonials"></section>
<h2 class="abs heading section-title" style="top:2541px">Testimonials</h2>
<svg class="abs quote-icon" width="46" height="36" viewBox="0 0 46 36"><path d="M0 36 V18 Q0 2 18 0 V8 Q9 10 9 18 H18 V36 Z M26 36 V18 Q26 2 44 0 V8 Q35 10 35 18 H44 V36 Z" fill="#ff6a00"/></svg>
<p class="abs quote-text">Teo's professionalism and dedication to his field is remarkable as is his strength and confidence as a coach. A careful listener, Mr. Varandel helped each of the training participants individually and uniquely, focused on developing confident skilled coaches...</p>
<div class="abs avatar" role="img" aria-label="Portrait of the client giving the testimonial"></div>
<p class="abs person-name">Mr. LV.</p>
<p class="abs person-role">Training Director, Executive Search and HR Consulting, China</p>
<div class="abs dots"><span class="dot"></span><span class="dot dot--on"></span><span class="dot"></span></div>

<footer>
  <div class="abs footer-brand">
    <div class="footer-mark"></div>
    <div class="footer-name">Bright Harbor</div>
    <div class="footer-tag">Consulting · Training · Coaching</div>
  </div>
  <div class="abs socials"><span class="social"></span><span class="social social--muted"></span><span class="social social--muted"></span></div>
  <p class="abs footer-mail">&#9993;&nbsp; info@brightharbor.example</p>
  <div class="abs footer-line"></div>
  <p class="abs copyright">© All Copyrights Reserved 2015</p>
</footer>

</body>
</html>
```